Moravel Aesthetic Doctor

I require an elegant, luxurious looking business card for my aesthetic business. I am a doctor and that will set me aside from competitors. I am planning to provide home and spa based treatments to clients with high expectations. I have attached my logo.

```html
<!DOCTYPE html>
<html lang="en">
<head>
<meta charset="utf-8">
<title>Moravel Aesthetic Doctor – Business Card</title>
<link rel="stylesheet" href="https://fonts.googleapis.com/css2?family=Arimo:wght@400;700&display=swap">
<style>
  :root {
    --stage: #000000;
    --card: #323234;
    --card-edge: #3a3a3c;
    --grey-text: #bfc0c2;
    --light-text: #f2f2f2;
    --accent: #4fb6ea;
    --divider: #4a4a4d;
  }
  * { margin: 0; padding: 0; box-sizing: border-box; }
  html, body {
    width: 1200px; height: 900px; overflow: hidden;
    background: var(--stage);
    font-family: "Arimo", Arial, sans-serif;
  }
  .stage { position: relative; width: 1200px; height: 900px; }
  .card {
    position: absolute; width: 458px; height: 282px;
    background: var(--card);
    border-radius: 14px;
    border: 1px solid var(--card-edge);
    overflow: hidden;
  }
  .card--front { left: 137px; top: 265px; }
  .card--back { left: 625px; top: 268px; }
  .abs { position: absolute; white-space: nowrap; }

  /* brand mark */
  .brand { position: absolute; display: flex; align-items: center; }
  .brand__ring { border: 2px solid var(--grey-text); border-radius: 50%; flex: none; }
  .brand__name { color: var(--grey-text); font-weight: 400; white-space: nowrap; }
  .brand--small { left: 18px; top: 112px; gap: 10px; }
  .brand--small .brand__ring { width: 48px; height: 48px; }
  .brand--small .brand__name { font-size: 14px; line-height: 16px; letter-spacing: 0.8px; }
  .brand--large { left: 0; right: 0; top: 52px; justify-content: center; gap: 14px; }
  .brand--large .brand__ring { width: 80px; height: 80px; }
  .brand--large .brand__name { font-size: 22px; line-height: 28px; letter-spacing: 1px; }

  .divider { left: 216px; top: 69px; width: 1px; height: 144px; background: var(--divider); }

  .name { left: 231px; top: 66px; font-size: 19px; font-weight: 700; color: var(--grey-text); }
  .name .post { font-size: 12px; font-weight: 400; color: var(--accent); margin-left: 3px; }
  .credential { left: 231px; top: 88px; font-size: 14px; line-height: 17px; color: var(--accent); }

  .contact { left: 231px; top: 136px; font-size: 13.5px; color: var(--grey-text); }
  .contact li { list-style: none; display: flex; align-items: center; gap: 5px; height: 17.5px; }
  .contact svg { width: 12px; height: 12px; fill: none; stroke: var(--accent); stroke-width: 1.4; flex: none; }

  .social { left: 233px; top: 198px; display: flex; gap: 4px; }
  .social span { width: 16px; height: 16px; border-radius: 50%; background: var(--accent); }
  .social span + span { background: #c6507a; }

  .services-title {
    left: 0; right: 0; top: 172px; text-align: center;
    font-size: 14px; color: var(--light-text); letter-spacing: 0.2px;
  }
  .services {
    left: 0; right: 0; top: 205px; text-align: center;
    font-size: 14px; line-height: 17px; color: var(--light-text);
  }
  .services .dot { margin: 0 7px; font-size: 10px; vertical-align: 1px; }
</style>
</head>
<body>
<main class="stage">
  <section class="card card--front">
    <div class="brand brand--small">
      <span class="brand__ring"></span>
      <span class="brand__name">MORAVEL<br>AESTHETIC<br>DOCTOR</span>
    </div>
    <div class="abs divider"></div>
    <p class="abs name">Dr Elena Marsh<span class="post">MRCPCH MD</span></p>
    <p class="abs credential">Australasian Diploma of<br>Aesthetic Medicine</p>
    <ul class="abs contact">
      <li><svg viewBox="0 0 12 12"><path d="M2 1.5l2 0 1 2.5-1.3 1a6 6 0 0 0 3.3 3.3l1-1.3 2.5 1v2a1 1 0 0 1-1 1A9 9 0 0 1 1 2.5a1 1 0 0 1 1-1z"/></svg>0800 555 014</li>
      <li><svg viewBox="0 0 12 12"><rect x="1" y="2.5" width="10" height="7"/><path d="M1 2.5l5 4 5-4"/></svg>elena@moravel.co.nz</li>
      <li><svg viewBox="0 0 12 12"><circle cx="6" cy="6" r="5"/><path d="M1 6h10M6 1c-2.5 3-2.5 7 0 10M6 1c2.5 3 2.5 7 0 10"/></svg>www.moravel.co.nz</li>
    </ul>
    <div class="abs social"><span></span><span></span></div>
  </section>

  <section class="card card--back">
    <div class="brand brand--large">
      <span class="brand__ring"></span>
      <span class="brand__name">MORAVEL<br>AESTHETIC DOCTOR</span>
    </div>
    <p class="abs services-title">HOME AND SPA BASED TREATMENTS</p>
    <p class="abs services">
      Dermal injectables<span class="dot">●</span>Plasma facials<span class="dot">●</span>Microneedling<br>
      Skin boosters<span class="dot">●</span>Excessive sweating
    </p>
  </section>
</main>
</body>
</html>
```